Vernac Law Business cards and stationary design project

We are looking for a stationary design for business cards (double sided), 8x10, 5x7, and legal and standard envelopes.

We would like the design to match the logo that we have already.
Color palate preferred is Teal, White, grey and any others that will look good for a professional law firm.

We would like this statement: "RELATIONSHIPS. RESPECT. RESULT" to be on the back of the business cards and maybe on the stationary if it looks good.

Please see link to website for more information: www.vernac-law.example

Target Market(s)

Potential clients that need Attorney services.

Industry/Entity Type

Law Firm

Contact Information for Business Card

We would like the front and back to be two different colors. Current business cards are teal front, grey back and are a vertical design. We are open to options with colors.

Font styles to use
Serif

Colors
33a6d7
33b8a4
b9b9b9
5c5c5c

Requirements
Must have
• Logo supplied needs to go on the card and stationary.
• Match website color palate, www.vernac-law.example
• Be professional and not too wordy.
• Criminal Law, Civil Litigation, Personal Injury, Restraining Orders need to be on the card.
Nice to have
• RELATIONSHIPS. RESPECT. RESULTS. on the back of the card.
Should not have
• Not be too busy/wordy or too flashy.

```html
<!DOCTYPE html>
<html lang="en">
<head>
<meta charset="utf-8">
<title>Vernac Law – Business Card</title>
<link href="https://fonts.googleapis.com/css2?family=Source+Sans+3:wght@400;600;700&display=swap" rel="stylesheet">
<style>
  :root {
    --backdrop: #939393;
    --paper: #ffffff;
    --teal: #127f8c;
    --deep-teal: #0b4246;
    --faint-teal: #255458;
    --ink: #111111;
    --white: #ffffff;
  }
  * { margin: 0; padding: 0; box-sizing: border-box; }
  html, body { width: 1200px; height: 900px; overflow: hidden; }
  body {
    background: var(--backdrop);
    font-family: "Source Sans 3", "Myriad Pro", Arial, sans-serif;
    position: relative;
  }
  .card {
    position: absolute;
    top: 170px;
    width: 347px;
    height: 561px;
    text-align: center;
  }
  .card--front { left: 259px; background: var(--paper); }
  .card--back { left: 641px; background: var(--deep-teal); overflow: hidden; }

  .line { position: absolute; left: 0; right: 0; }

  .brand-mark {
    position: absolute; left: 153px; top: 56px;
    width: 40px; height: 40px; background: var(--teal);
  }
  .brand-name {
    top: 142px; font-size: 30px; font-weight: 600;
    color: var(--teal); letter-spacing: 1px;
  }
  .person-name { top: 216px; font-size: 22px; font-weight: 700; color: var(--teal); }
  .person-title { top: 241px; font-size: 16px; color: var(--ink); }

  .contact {
    top: 296px; font-size: 16px; color: var(--ink); line-height: 23px;
  }
  .contact li { list-style: none; display: flex; justify-content: center; align-items: center; gap: 3px; }
  .contact svg { width: 11px; height: 11px; fill: var(--teal); }

  .address { top: 405px; font-size: 16px; color: var(--ink); line-height: 17px; }
  .practice {
    top: 463px; font-size: 16px; font-weight: 600; color: var(--teal); line-height: 20.5px;
  }

  .backdrop-square {
    position: absolute; left: 30px; top: 30px;
    width: 320px; height: 365px; background: var(--faint-teal);
  }
  .back-name {
    top: 406px; font-size: 40px; font-weight: 600; color: var(--white); letter-spacing: 1px;
  }
  .tagline {
    top: 494px; font-size: 17.5px; font-weight: 600; color: var(--white);
  }
</style>
</head>
<body>
  <section class="card card--front">
    <div class="brand-mark"></div>
    <p class="line brand-name">Vernac Law</p>
    <p class="line person-name">Daniel Mercer</p>
    <p class="line person-title">Managing Director</p>
    <ul class="line contact">
      <li><svg viewBox="0 0 12 12"><path d="M2.5 1l2 2.2-1 1.3c.7 1.4 1.7 2.4 3 3l1.3-1L10 8.5 9 11C4.8 10.6 1.4 7.2 1 3z"/></svg>(044)-456-7890</li>
      <li><svg viewBox="0 0 12 12"><rect x="3" y="1" width="6" height="3"/><rect x="1" y="4.5" width="10" height="6.5" rx="1"/></svg>123-456-7890</li>
      <li><svg viewBox="0 0 12 12"><path d="M1 2.5h10v7H1z M1.5 3l4.5 3.5L10.5 3" stroke="#fff" stroke-width=".8"/></svg>info@youremail.com</li>
      <li><svg viewBox="0 0 12 12"><circle cx="6" cy="6" r="5.2"/></svg>www.website.com</li>
    </ul>
    <p class="line address">12345, Address Goes Here<br>Country Name, 123456</p>
    <p class="line practice">Practice areas, Criminal Law,<br>Civil Litigation/Personal Injury<br>Restraining Orders</p>
  </section>

  <section class="card card--back">
    <div class="backdrop-square"></div>
    <p class="line back-name">Vernac Law</p>
    <p class="line tagline">RELATIONSHIPS. RESPECT. RESULT</p>
  </section>
</body>
</html>
```